Graphical PowerPoint Presentation Design

Hey guys, I need a presentation for an important client regarding strategic marketing plan, related to the pharmaceutical products. I will be providing a draft, and you will need to create out of it an creative, engaging, visually attractive and professional presentation consisting around 10 slides which will cover all the major points mentioned in the presentation, I would like to include as well the image related to each major point.
I would prefer the presentation done with PREZI software.
This has to be delivered on or before 3rd Dec 2018. For further info please post on the clarification board, or submit the entry so we can have a private chat.

Thank you!

Best Regards,
Nora

```html
<!DOCTYPE html>
<html lang="en">
<head>
<meta charset="utf-8">
<title>Business Plan – Pharmaceutical Marketing Deck</title>
<link href="https://fonts.googleapis.com/css2?family=Open+Sans:wght@400;600;700&family=Cinzel:wght@700&family=Kalam:wght@700&display=swap" rel="stylesheet">
<style>
:root{
  --stage:#c8cad6;
  --slide:#f4f4f6;
  --ink:#2b2d3c;
  --plum:#6e6680;
  --plum-light:#8a8399;
  --grey:#d9d9de;
  --text:#6d6d78;
  --white:#ffffff;
  --accent:#e07a3a;
  --num:#4a4a55;
}
*{box-sizing:border-box;margin:0;padding:0}
html,body{width:1200px;height:543px;overflow:hidden}
body{background:var(--stage);font-family:"Open Sans",Arial,sans-serif;position:relative}
.slide{position:absolute;width:263px;height:148px;background:linear-gradient(160deg,#fafafb,var(--slide) 60%,#e9e9ee);overflow:hidden;box-shadow:0 1px 2px rgba(0,0,0,.15)}
.slide.selected{outline:3px solid var(--accent);outline-offset:1px}
.num{position:absolute;font-size:11px;color:var(--num)}
.abs{position:absolute}
.photo{position:absolute}
.t-title{font-size:5px;font-weight:700;color:var(--ink);line-height:1.3}
.t-body{font-size:3.6px;line-height:1.45;color:var(--text)}
.t-white{color:var(--white)}
.year{position:absolute;font-size:9px;font-weight:600;color:var(--white)}
.year-note{position:absolute;font-size:3.5px;color:#e6e3ee}
.contents{font-family:"Cinzel",serif;font-size:11px;color:var(--ink)}
.part-line{font-size:5px;color:var(--ink);line-height:17px;white-space:nowrap}
.part-box{position:absolute;background:var(--grey);text-align:center}
.part-box b{font-family:"Kalam",cursive;font-size:14px;color:var(--ink);letter-spacing:1px}
.tab{position:absolute;background:var(--ink);color:var(--white);font-size:4px;font-weight:700;text-align:center;padding:1px 6px;white-space:nowrap}
.box{position:absolute;border:1px solid #b9bfd0;background:var(--white)}
.icon{position:absolute;width:12px;height:12px;background:var(--ink);border-radius:2px}
.icon.plum{background:var(--plum)}
svg{position:absolute;left:0;top:0}
</style>
</head>
<body>

<!-- Row 1 -->
<section class="slide selected" style="left:20px;top:11px">
  <div class="photo" role="img" aria-label="Photo of a glass office tower seen from below" style="inset:0;background:linear-gradient(135deg,#1d2030,#4a4f62 45%,#2a2d3a 70%,#6b6f80)"></div>
  <svg width="263" height="148" viewBox="0 0 263 148"><polygon points="20,0 200,0 110,95" fill="rgba(255,255,255,.18)"/><polyline points="20,0 110,95 200,0" fill="none" stroke="rgba(255,255,255,.6)" stroke-width="1"/></svg>
  <h1 class="abs t-white" style="left:28px;top:12px;font-size:16px;font-weight:400">BUSINESS PLAN</h1>
  <div class="year" style="right:10px;top:116px">1995 &amp; 2017</div>
  <div class="year-note" style="right:10px;top:129px">Pharma marketing strategy</div>
</section>
<span class="num" style="left:22px;top:165px">1</span>

<section class="slide" style="left:324px;top:11px">
  <svg width="263" height="148" viewBox="0 0 263 148"><polygon points="210,0 263,0 263,148 193,148" fill="var(--plum)"/></svg>
  <div class="abs contents" style="left:27px;top:50px">Contents</div>
  <div class="abs" style="left:104px;top:38px">
    <div class="part-line"><b>Part 01</b>&nbsp;&nbsp;<span class="t-body">Market review</span></div>
    <div class="part-line"><b>Part 02</b>&nbsp;&nbsp;<span class="t-body">Target doctors</span></div>
    <div class="part-line"><b>Part 03</b>&nbsp;&nbsp;<span class="t-body">Product plan</span></div>
    <div class="part-line"><b>Part 04</b>&nbsp;&nbsp;<span class="t-body">Sales goals</span></div>
  </div>
  <div class="year" style="right:10px;top:116px">1995 &amp; 2017</div>
  <div class="year-note" style="right:10px;top:129px">Pharma marketing strategy</div>
</section>
<span class="num" style="left:326px;top:165px">2</span>

<section class="slide" style="left:627px;top:11px">
  <svg width="263" height="148" viewBox="0 0 263 148"><polygon points="214,0 263,0 263,148 194,148" fill="var(--plum)"/></svg>
  <div class="part-box" style="left:57px;top:64px;width:90px;height:24px;line-height:24px"><b>PART</b></div>
  <div class="abs t-body" style="left:80px;top:90px">Market review</div>
  <div class="year" style="right:10px;top:116px">1995 &amp; 2017</div>
  <div class="year-note" style="right:10px;top:129px">Pharma marketing strategy</div>
</section>
<span class="num" style="left:629px;top:165px">3</span>

<section class="slide" style="left:929px;top:11px">
  <div class="abs t-title" style="left:18px;top:55px">Add your title</div>
  <p class="abs t-body" style="left:18px;top:64px;width:82px">Drug sales grew in all regions, led by clinics and retail chains.</p>
  <svg width="263" height="148" viewBox="0 0 263 148">
    <polygon points="116,34 153,34 153,100 134,112 116,100" fill="var(--ink)"/>
    <polygon points="156,34 193,34 193,100 174,112 156,100" fill="var(--plum)"/>
    <polygon points="196,34 233,34 233,100 214,112 196,100" fill="var(--ink)"/>
    <circle cx="237" cy="133" r="5" fill="var(--plum-light)"/>
    <circle cx="247" cy="133" r="5" fill="var(--ink)"/>
  </svg>
  <div class="abs" style="left:120px;top:42px;width:30px"><div class="t-title t-white">Add your title</div><div class="t-body t-white">Clinic reach up in every region</div></div>
  <div class="abs" style="left:160px;top:42px;width:30px"><div class="t-title t-white">Add your title</div><div class="t-body t-white">New drugs win strong share</div></div>
  <div class="abs" style="left:200px;top:42px;width:30px"><div class="t-title t-white">Add your title</div><div class="t-body t-white">Pharmacy orders rise again</div></div>
</section>
<span class="num" style="left:931px;top:165px">4</span>

<!-- Row 2 -->
<section class="slide" style="left:20px;top:192px">
  <div class="box" style="left:28px;top:42px;width:104px;height:30px"></div>
  <div class="tab" style="left:58px;top:36px">Add your title</div>
  <p class="abs t-body" style="left:34px;top:50px;width:92px">Reach doctors through visits, events and trusted medical journals</p>
  <div class="box" style="left:28px;top:92px;width:104px;height:24px"></div>
  <div class="tab" style="left:58px;top:86px">Add your title</div>
  <p class="abs t-body" style="left:34px;top:99px;width:92px">Train sales reps on each new product and its patient benefit</p>
  <div class="photo" role="img" aria-label="Photo of team hands joined together in a circle" style="left:160px;top:33px;width:78px;height:99px;background:linear-gradient(150deg,#e8e8ea,#b8a394 45%,#3d3e48 80%)"></div>
</section>
<span class="num" style="left:22px;top:346px">5</span>

<section class="slide" style="left:324px;top:192px">
  <svg width="263" height="148" viewBox="0 0 263 148" fill="var(--ink)">
    <circle cx="42" cy="78" r="6"/><circle cx="48" cy="96" r="5"/><circle cx="60" cy="104" r="4.5" fill="var(--plum)"/>
    <circle cx="74" cy="100" r="3.5"/><circle cx="84" cy="90" r="3.5"/><circle cx="93" cy="77" r="3.5" fill="var(--plum)"/>
    <circle cx="103" cy="64" r="4"/><circle cx="116" cy="52" r="4"/><circle cx="130" cy="42" r="4.5" fill="var(--plum)"/>
    <circle cx="145" cy="34" r="5"/><circle cx="162" cy="31" r="5.5" fill="var(--plum)"/><circle cx="178" cy="36" r="6"/>
    <circle cx="193" cy="48" r="7" fill="var(--plum)"/><circle cx="203" cy="66" r="8" fill="var(--plum-light)"/>
  </svg>
  <p class="abs t-body" style="left:80px;top:36px;width:34px">Step one: study the market and rivals</p>
  <p class="abs t-body" style="left:80px;top:66px;width:26px">Step two: pick key doctors</p>
  <p class="abs t-body" style="left:118px;top:64px;width:34px">Step three: launch the campaign</p>
  <p class="abs t-body" style="left:126px;top:88px;width:36px">Step four: track sales and refine</p>
</section>
<span class="num" style="left:326px;top:346px">6</span>

<section class="slide" style="left:627px;top:192px">
  <div class="abs t-title" style="left:23px;top:58px">Add your title</div>
  <p class="abs t-body" style="left:23px;top:66px;width:58px">Open new sales points in city hospitals</p>
  <div class="photo" role="img" aria-label="Illustration of location pins on a round platform" style="left:87px;top:35px;width:74px;height:92px;background:linear-gradient(180deg,#f4f4f6 0%,#5a5c6a 40%,#8d8f98 100%)"></div>
  <div class="abs t-title" style="left:170px;top:26px">Add your title</div>
  <p class="abs t-body" style="left:170px;top:34px;width:72px">Grow pharmacy coverage in the north region</p>
  <div class="abs t-title" style="left:183px;top:74px">Add your title</div>
  <p class="abs t-body" style="left:183px;top:82px;width:62px">Partner with regional drug wholesalers</p>
</section>
<span class="num" style="left:629px;top:346px">7</span>

<section class="slide" style="left:929px;top:192px">
  <div class="photo" role="img" aria-label="Photo of people signing a business document" style="left:33px;top:38px;width:67px;height:42px;background:linear-gradient(120deg,#8d93a6,#d8dbe3 55%,#5b6071)"></div>
  <div class="abs" style="left:100px;top:38px;width:68px;height:42px;background:var(--plum)"></div>
  <div class="abs" style="left:168px;top:38px;width:71px;height:42px;background:var(--ink)"></div>
  <div class="abs" style="left:174px;top:47px;width:60px"><div class="t-title t-white">Add your title</div><div class="t-body t-white">Supply deals signed with hospital groups</div></div>
  <div class="tab" style="left:26px;top:94px">Add your title</div>
  <p class="abs t-body" style="left:26px;top:106px;width:205px">Long term contracts with hospitals keep product supply steady and build trust with prescribing doctors across the region</p>
</section>
<span class="num" style="left:931px;top:346px">8</span>

<!-- Row 3 -->
<section class="slide" style="left:20px;top:373px">
  <svg width="263" height="148" viewBox="0 0 263 148"><polygon points="213,0 263,0 263,148 192,148" fill="var(--plum)"/></svg>
  <div class="part-box" style="left:78px;top:64px;width:73px;height:25px;line-height:25px"><b>PART</b></div>
  <div class="abs t-body" style="left:94px;top:91px">Product plan</div>
  <div class="year" style="right:10px;top:116px">1995 &amp; 2017</div>
  <div class="year-note" style="right:10px;top:129px">Pharma marketing strategy</div>
</section>
<span class="num" style="left:22px;top:527px">9</span>

<section class="slide" style="left:324px;top:373px">
  <div class="icon" style="left:24px;top:48px"></div>
  <div class="abs" style="left:40px;top:47px;width:44px"><div class="t-title">Add your title</div><div class="t-body">Prescription drug line and its price</div></div>
  <div class="icon plum" style="left:96px;top:48px"></div>
  <div class="abs" style="left:112px;top:47px;width:44px"><div class="t-title">Add your title</div><div class="t-body">Awards for quality and safety</div></div>
  <div class="icon" style="left:168px;top:48px"></div>
  <div class="abs" style="left:184px;top:47px;width:44px"><div class="t-title">Add your title</div><div class="t-body">Links with clinics and labs</div></div>
  <div class="icon plum" style="left:24px;top:90px"></div>
  <div class="abs" style="left:40px;top:89px;width:44px"><div class="t-title">Add your title</div><div class="t-body">Trophy goals for the sales team</div></div>
  <div class="icon" style="left:96px;top:90px"></div>
  <div class="abs" style="left:112px;top:89px;width:44px"><div class="t-title">Add your title</div><div class="t-body">Patient data kept safe</div></div>
  <div class="icon plum" style="left:168px;top:90px"></div>
  <div class="abs" style="left:184px;top:89px;width:44px"><div class="t-title">Add your title</div><div class="t-body">Online reach to doctors</div></div>
</section>
<span class="num" style="left:326px;top:527px">10</span>

<section class="slide" style="left:627px;top:373px">
  <div class="abs t-title" style="left:23px;top:50px">Key point</div>
  <p class="abs t-body" style="left:23px;top:58px;width:115px">Each sales rep serves forty doctors and reports weekly on new prescriptions and samples given.</p>
  <div class="abs t-title" style="left:23px;top:92px">Key point</div>
  <p class="abs t-body" style="left:23px;top:100px;width:115px">Customer service answers pharmacy questions within one day and tracks every order.</p>
  <div class="photo" role="img" aria-label="Illustration of an office worker at a desk" style="left:150px;top:40px;width:86px;height:71px;background:linear-gradient(180deg,#eceaee 0%,#d9ccc6 50%,#a77b57 51%,#8a6444)"></div>
</section>
<span class="num" style="left:629px;top:527px">11</span>

<section class="slide" style="left:929px;top:373px">
  <div class="photo" role="img" aria-label="Photo of a fruit on books before a chalkboard" style="left:14px;top:28px;width:71px;height:42px;background:linear-gradient(160deg,#2e4a3c,#3d5e4b 60%,#a5672e)"></div>
  <div class="photo" role="img" aria-label="Photo of stacked oranges on a table" style="left:96px;top:28px;width:71px;height:42px;background:linear-gradient(160deg,#2e4a3c,#c77a2a 70%,#8d5320)"></div>
  <div class="photo" role="img" aria-label="Photo of glass jars on a shelf" style="left:178px;top:28px;width:71px;height:42px;background:linear-gradient(160deg,#3a4f46,#8f8f80 60%,#c6c0a8)"></div>
  <p class="abs t-body" style="left:14px;top:74px;width:71px">Health education for patients and families</p>
  <p class="abs t-body" style="left:96px;top:74px;width:71px">Vitamin line for daily wellness</p>
  <p class="abs t-body" style="left:178px;top:74px;width:71px">Lab tested quality in each batch</p>
  <div class="icon" style="left:14px;top:109px"></div><div class="abs t-title" style="left:30px;top:112px">Add your title</div>
  <div class="icon plum" style="left:96px;top:109px"></div><div class="abs t-title" style="left:112px;top:112px">Add your title</div>
  <div class="icon" style="left:178px;top:109px"></div><div class="abs t-title" style="left:194px;top:112px">Add your title</div>
</section>
<span class="num" style="left:931px;top:527px">12</span>

</body>
</html>
```